Systems and Technology Consultants - Website

Design & Build a website for a new company which operates in the Systems and Technology space for Transportation, Government and Commercial sectors.

Overall design should be minimalist in nature.
Should also have a feed that provides news and event updates on the main page.
Logo has already been awarded and should be incorporated into the site.

We like the overall layout, functionality and simplicity of the below sites. Submitted designs could be similar to or a combination of the aspects on these sites, or perhaps a whole different concept - we are open to new ideas.
Norvique.com
Teblo.it

Update 1 Dated 27 May 2014

All I am moving away from the Teblo.it website and would like it to be more aligned with Norvique.com not only in layout but in functionality. I will be extending the deadline of this design brief for two weeks to incorporate additional requirements and will add addtional funding to the project.

Apologies for not having more information available to provide but with so many submissions its getting confusing.

Thanks Derek

Please note that the brief has been updated and the deadline has been extended.

Important: We will need two language versions of the website, English and Arabic; the website is hosted on HostPelican

Hello All, Thank you for your submissions. We have narrowed it down to the final 6 designers and I just wanted to take a moment and provide a bit of feedback regarding the concepts that we like and the modifications we are looking for. First, let me mention some of the design functions we like. - At the top of the homepage we really like the "region" or "language" tab so that the website can be viewed in both English and Arabic. - We like the homepage to have clear color variation so that the different sections of the homepage are distinct. Additionally, we like the bottom portion of the homepage to be in red. We feel that draws attention to our contact information. Again, we would like the colors to integrate black, gray-scale, red, etc. - Having a search tab at the top of the home page, or integrated into the main image, so that the site is easy to navigate. - We especially like the main image to have the scrolling tabs at the bottom so it is easy to browse the services offered (Consultancy, Solutions Architecture, Masters Systems Integration, Independent Design Review). - In regards to the services offered tab we really like the idea that a few people presented that have the outside of our logo with an icon in the middle of consultancy, solutions, etc., etc. Secondly, as mentioned in our brief we really enjoy the design of norvique site. Specially, we enjoy the strong iconic images they use, the way the tabs at the top scroll easily, and contact us page that generates an email. Lastly, I've included some photos of the concept we have been working on. What we are trying to demonstrate is how our company offers a range of services that are essentially linked together. We provide individual services that when combined present the full service package. We would like this concept to be integrated into the over concept of our website. Please feel free to ask for clarification of any of the above points or contact us if you have any additional questions. We appreciate all of your hard work and are very excited to see the updated designs. Best, Marta Vennick Quelbrant Senior Program Manager marta.vennick@quelbrant-example.com

Industry/Entity Type

Government

Font styles to use
Serif
Sans Serif

Requirements
Must have
• Must work on/adapt to various/mobile devices (responsive)
Must be simple and straightforward
Colors should be in line/matching with logo
2 language versions: English and Arabic (no Thai)
Services should be the first group/row of items after/below the main image
Note: the website will be hosted by hostpelican
Nice to have
• Submit feedback form
What's New section
The banner at the bottom of the site should not be too large; we would like a narrow one more
It would be nice if the header/top banner (with Home, About, etc. tabs) could stay in place as you scroll down (like Norvique and Chatterloop)
We will likely only use one image with a Company slogan on the Home page rather than a carousel of images to rotate through
Should not have
• This is the existing website: http://www.quelbrant-example.org
We do not like the animation, the way the banner icons/titles bounce
Not simple enough, we don't like the functionality or how pages load so slowly
We do not like the logo centered - it should be at the left
The banner and its tabs should not be towards the right, we would like them to be centered, to go all the way across and to be below the logo

```html
<!DOCTYPE html>
<html lang="en">
<head>
<meta charset="utf-8">
<title>Quelbrant International</title>
<link href="https://fonts.googleapis.com/css2?family=Montserrat:wght@700&family=Roboto:wght@400;500;700&family=Roboto+Condensed:wght@400&display=swap" rel="stylesheet">
<style>
:root{
  --navy:#161a2c;
  --red:#d42727;
  --white:#ffffff;
  --ink:#444a52;
  --muted:#8a8f96;
  --accent:#e2461d;
  --sky:#0ba7da;
  --black:#0b0b0c;
  --rule:#e1e3e6;
}
*{margin:0;padding:0;box-sizing:border-box}
html,body{width:1051px;height:1200px;overflow:hidden;background:var(--white)}
body{font-family:"Roboto",sans-serif;color:var(--ink);position:relative}
.site-header{position:absolute;top:0;left:0;width:1051px;height:73px;background:var(--navy)}
.brand{position:absolute;top:26px;left:112px;display:flex;align-items:center;gap:8px}
.brand-mark{width:14px;height:14px;background:var(--red)}
.brand-name{font-family:"Roboto",sans-serif;font-weight:700;font-size:17px;letter-spacing:3px;color:var(--red)}
.main-nav{position:absolute;top:31px;left:0;width:1051px;height:14px;font-size:11px;line-height:14px;color:var(--white)}
.main-nav span{position:absolute;top:0;white-space:nowrap}
.main-nav .has-sub::after{content:"";display:inline-block;margin-left:4px;border:3px solid transparent;border-top-color:var(--white);vertical-align:-1px}
.nav-search{position:absolute;top:29px;left:909px;height:18px;border-left:1px solid #aaa;padding-left:8px}
.hero{position:absolute;top:73px;left:0;width:1051px;height:311px;background:linear-gradient(90deg,#1b2440 0%,#243a6e 45%,#1a2747 100%)}
.hero-photo{position:absolute;right:85px;top:10px;width:420px;height:301px;background:radial-gradient(ellipse at 70% 60%,#7d7a5a 0%,#4a5a7a 50%,rgba(36,58,110,0) 75%)}
.hero-title{position:absolute;top:96px;left:114px;font-family:"Montserrat",sans-serif;font-weight:700;font-size:29px;line-height:44px;letter-spacing:1px;color:var(--white)}
.btn-more{position:absolute;top:237px;left:112px;width:118px;height:27px;background:var(--red);border-radius:2px;color:var(--white);font-family:"Montserrat",sans-serif;font-weight:700;font-size:9.5px;letter-spacing:1.5px;display:flex;align-items:center;justify-content:center;gap:5px}
.services{position:absolute;top:384px;left:0;width:1051px;height:261px;background:var(--red);color:var(--white)}
.service{position:absolute;top:28px;width:240px;text-align:center}
.service svg{display:block;margin:0 auto}
.service h3{font-weight:500;font-size:15px;margin-top:14px}
.service p{font-size:9.5px;line-height:14px;margin-top:7px}
.solutions{position:absolute;top:678px;left:0;width:1051px}
.solution{position:absolute;width:250px}
.solution .photo{width:248px;height:122px}
.solution h4{font-family:"Roboto Condensed",sans-serif;font-weight:400;font-size:14px;color:#5a5f66;margin-top:16px}
.solution p{font-size:9.5px;line-height:14px;margin-top:9px}
.news{position:absolute;top:934px;left:118px;width:813px;height:43px;border-top:1px solid var(--rule);border-bottom:1px solid var(--rule);display:flex;align-items:center;font-size:10px}
.news-label{font-family:"Roboto Condensed",sans-serif;font-size:13px;color:var(--muted);margin-right:8px}
.news-date{color:var(--muted);margin-right:7px}
.news-link{color:var(--accent)}
.news-arrows{position:absolute;right:8px;top:11px;display:flex;gap:6px}
.testimonial{position:absolute;top:1005px;left:0;width:1051px;height:147px;background:var(--sky);color:var(--white);text-align:center}
.quote-badge{position:absolute;top:-19px;left:507px}
.testimonial blockquote{position:absolute;top:29px;left:190px;width:672px;font-size:14.5px;line-height:19px;font-weight:400}
.cite{position:absolute;top:93px;left:715px;text-align:left}
.cite strong{display:block;font-size:11.5px;font-weight:500}
.cite span{display:block;font-size:9.5px;color:#bfe7f5;margin-top:2px}
.site-footer{position:absolute;top:1152px;left:0;width:1051px;height:48px;background:var(--black)}
.site-footer .brand{top:16px;left:110px}
.site-footer .brand-mark{background:var(--white);width:11px;height:11px}
.site-footer .brand-name{color:var(--white);font-size:12px}
.copyright{position:absolute;top:20px;right:120px;font-size:9.5px;color:#d6d6d6}
</style>
</head>
<body>
<header class="site-header">
  <div class="brand"><span class="brand-mark"></span><span class="brand-name">QUELBRANT</span></div>
  <nav class="main-nav">
    <span style="left:445px">HOME</span>
    <span class="has-sub" style="left:498px">ABOUT US</span>
    <span class="has-sub" style="left:573px">BUSINESS UNITS</span>
    <span class="has-sub" style="left:678px">SERVICES</span>
    <span class="has-sub" style="left:749px">LOCATIONS</span>
    <span style="left:831px">CONTACT US</span>
  </nav>
  <div class="nav-search">
    <svg width="16" height="16" viewBox="0 0 16 16"><circle cx="6.5" cy="6.5" r="5" fill="none" stroke="#fff" stroke-width="1.4"/><line x1="10.2" y1="10.2" x2="15" y2="15" stroke="#fff" stroke-width="1.6"/></svg>
  </div>
</header>

<section class="hero">
  <div class="hero-photo" role="img" aria-label="Engineer in hard hat and safety vest holding a laptop, in front of a blurred server room"></div>
  <h1 class="hero-title">FINANCIAL AND<br>TECHNOLOGY SPACE FOR<br>TRANSPORTATION</h1>
  <div class="btn-more">LEARN MORE
    <svg width="18" height="10" viewBox="0 0 18 10"><polyline points="1,1 6,5 1,9" fill="none" stroke="#fff" stroke-width="1.4"/><polyline points="8,1 13,5 8,9" fill="none" stroke="#fff" stroke-width="1.4"/></svg>
  </div>
</section>

<section class="services">
  <div class="service" style="left:105px">
    <svg width="86" height="96" viewBox="0 0 86 96"><circle cx="43" cy="48" r="38" fill="none" stroke="#fff" stroke-width="6"/><circle cx="43" cy="48" r="12" fill="none" stroke="#fff" stroke-width="4"/><g stroke="#fff" stroke-width="4"><line x1="43" y1="28" x2="43" y2="33"/><line x1="43" y1="63" x2="43" y2="68"/><line x1="23" y1="48" x2="28" y2="48"/><line x1="58" y1="48" x2="63" y2="48"/></g></svg>
    <h3>Engineearing</h3>
    <p>Lorem ipsum dolorSit amet consecteturAdipsicing elit,<br>ed do euismodTempor incidunt Labore et dolor<br>Magna aliqua.Lorem ipsum dolorSit amet consec-<br>teturAdipsicing elit,ed do euismodTempor incidunt</p>
  </div>
  <div class="service" style="left:392px">
    <svg width="86" height="96" viewBox="0 0 86 96"><circle cx="43" cy="48" r="38" fill="none" stroke="#fff" stroke-width="6"/><g fill="none" stroke="#fff" stroke-width="2"><rect x="29" y="42" width="7" height="7"/><rect x="39" y="42" width="7" height="7"/><rect x="49" y="42" width="7" height="7"/><rect x="29" y="52" width="7" height="7"/><rect x="39" y="52" width="7" height="7"/><rect x="49" y="52" width="7" height="7"/><rect x="41" y="32" width="7" height="7"/><rect x="51" y="30" width="7" height="7"/></g></svg>
    <h3>Quelbrant Consulting</h3>
    <p>Lorem ipsum dolorSit amet consecteturAdipsicing elit,<br>ed do euismodTempor incidunt Labore et dolor<br>Magna aliqua.Lorem ipsum dolor<br>Sit amet consecteturAdipsicing elit,ed do euismod-<br>Tempor incidunt</p>
  </div>
  <div class="service" style="left:693px">
    <svg width="86" height="96" viewBox="0 0 86 96"><circle cx="43" cy="48" r="38" fill="none" stroke="#fff" stroke-width="6"/><rect x="27" y="36" width="32" height="24" fill="none" stroke="#fff" stroke-width="3"/><circle cx="44" cy="48" r="6" fill="none" stroke="#fff" stroke-width="2.5"/><line x1="48" y1="52" x2="54" y2="58" stroke="#fff" stroke-width="3"/></svg>
    <h3>Maintenance</h3>
    <p>Lorem ipsum dolorSit amet consecteturAdipsicing elit,<br>ed do euismodTempor incidunt Labore et dolor<br>Magna aliqua.Lorem ipsum dolorSit amet consec-<br>teturAdipsicing elit,ed do euismodTempor incidunt</p>
  </div>
</section>

<section class="solutions">
  <article class="solution" style="left:110px">
    <div class="photo" role="img" aria-label="Two builders reviewing plans under a timber roof frame" style="background:linear-gradient(160deg,#c99a62,#8c6a45 60%,#4c5f82)"></div>
    <h4>Business Process Outsourcing</h4>
    <p>Lorem ipsum dolorSit amet consecteturAdipsicing elit,<br>ed do euismodTempor incidunt Labore et dolor<br>Magna aliqua.Lorem ipsum dolorSit amet consecteturAd-<br>ipsicing elit,ed do euismodTempor incidunt</p>
  </article>
  <article class="solution" style="left:400px">
    <div class="photo" role="img" aria-label="Inspectors in hard hats surveying a damaged site" style="background:linear-gradient(180deg,#7c9ac9,#9a9486 55%,#5b5447)"></div>
    <h4>App. Development &amp; Maintenance</h4>
    <p>Lorem ipsum dolorSit amet consecteturAdipsicing elit,<br>ed do euismodTempor incidunt Labore et dolor<br>Magna aliqua.Lorem ipsum dolorSit amet consecteturAd-<br>ipsicing elit,ed do euismodTempor incidunt</p>
  </article>
  <article class="solution" style="left:685px;top:-3px">
    <div class="photo" role="img" aria-label="Modern rotating boat lift structure under a cloudy sky" style="background:linear-gradient(180deg,#6f93cf,#c3cad3 55%,#6f8f4c)"></div>
    <h4>Human Capital Management Solution</h4>
    <p>Lorem ipsum dolorSit amet consecteturAdipsicing elit,<br>ed do euismodTempor incidunt Labore et dolor<br>Magna aliqua.Lorem ipsum dolorSit amet consecteturAd-<br>ipsicing elit,ed do euismodTempor incidunt</p>
  </article>
</section>

<div class="news">
  <span class="news-label">LATEST NEWS:</span>
  <span class="news-date">June 3, 2013</span>
  <span class="news-link">Harlow Ventures has signed up with Orvane Systems</span>
  <div class="news-arrows">
    <svg width="14" height="20" viewBox="0 0 14 20"><polyline points="11,2 3,10 11,18" fill="none" stroke="#e2461d" stroke-width="2"/></svg>
    <span style="width:1px;height:22px;background:var(--rule)"></span>
    <svg width="14" height="20" viewBox="0 0 14 20"><polyline points="3,2 11,10 3,18" fill="none" stroke="#e2461d" stroke-width="2"/></svg>
  </div>
</div>

<section class="testimonial">
  <svg class="quote-badge" width="36" height="40" viewBox="0 0 36 40"><polygon points="18,1 35,10 35,30 18,39 1,30 1,10" fill="#e2461d"/><path d="M10 23 q0-7 6-9 v3 q-3 1-3 4 h3 v5 h-6z M19 23 q0-7 6-9 v3 q-3 1-3 4 h3 v5 h-6z" fill="#fff"/></svg>
  <blockquote>Ledgerline ERP brought efficiency in our processes and facilitated the top management in better decision-making and monitoring by replacing manual processes with robust automation. We selected Orvane Systems because of its suitability for Tamsin Homes Limited business functions &amp; processes.</blockquote>
  <div class="cite"><strong>Karim Dalvi</strong><span>CFO, Tamsin Home Limited</span></div>
</section>

<footer class="site-footer">
  <div class="brand"><span class="brand-mark"></span><span class="brand-name">QUELBRANT</span></div>
  <div class="copyright">Copyrights © 2014Quelbrant.com - All Rights Reserved</div>
</footer>
</body>
</html>
```